Silver Harbor Med Spa Membership Sales Presentation to Clients handout

Hello! We are a high tech, Silver Harbor Med Spa in Dallas Texas that won Best Med Spa in Addison. I want my graphic membership form to represent that. We serve women and men so want it neutral but show cutting edge. Our colors are black, white, gray but would entertain your view. Having a challenge on making it easy to read as each membership gets more services yet one service a month. Thought maybe colorcoding what services are together? Definite road blocks on my end. I used Canva to lay out, but as you can see I am NOT gifted at graphic design. ;))

Target Market(s)

39-69

Industry/Entity Type

Medical Med Spa

Requirements
Must have
• cutting edge look

```html
<!DOCTYPE html>
<html lang="en">
<head>
<meta charset="utf-8">
<title>Silver Harbor Med Spa — Memberships</title>
<link rel="stylesheet" href="https://fonts.googleapis.com/css2?family=Poppins:wght@300;400;500;600&display=swap">
<style>
:root{
  --backdrop:#e6e6e6;
  --paper:#ffffff;
  --cyan:#00d9de;
  --cyan-soft:#aef3f8;
  --title:#13b4c4;
  --tick:#12c7d2;
  --line:#555a5c;
  --ink:#1c1c1c;
  --muted:#5a5a5a;
  --badge-red:#e0141e;
  --badge-dark:#111111;
}
*{box-sizing:border-box;margin:0;padding:0}
html,body{width:1200px;height:1200px;overflow:hidden;background:var(--backdrop)}
body{font-family:"Poppins",sans-serif;position:relative}
.sheet{position:absolute;left:174px;top:0;width:852px;height:1200px;background:var(--paper);overflow:hidden}
.brand{position:absolute;left:34px;top:60px;width:170px;display:flex;align-items:center;gap:8px}
.brand-dot{width:14px;height:14px;border-radius:50%;background:var(--ink);flex:none}
.brand-name{font-size:17px;font-weight:500;line-height:1.2;color:var(--ink);text-transform:uppercase;letter-spacing:.5px}
.title{position:absolute;left:206px;top:72px;width:470px;text-align:center;font-size:29px;font-weight:500;color:var(--title);letter-spacing:.2px;white-space:nowrap}
.badge{position:absolute;left:691px;top:29px;width:116px;height:116px;border-radius:50%;background:var(--badge-dark);border:5px solid var(--badge-red)}
.treat-bar{position:absolute;left:59px;top:167px;width:373px;height:26px;background:var(--cyan);color:#fff;font-weight:600;font-size:22px;line-height:26px;text-align:center}
.treat-sub{position:absolute;left:63px;top:196px;font-size:22px;color:var(--ink);letter-spacing:.3px}
.plans{position:absolute;left:27px;top:167px;border-collapse:collapse;table-layout:fixed}
.plans td,.plans th{border:1.5px solid var(--line);padding:0}
.plans th.spacer{border:none;border-bottom:1.5px solid var(--line);width:430px}
.plans th.tier{background:var(--cyan);color:#fff;font-weight:600;font-size:22px;line-height:24px;height:60px;text-align:center}
.plans th.tier.good{width:110px}.plans th.tier.better{width:118px}.plans th.tier.best{width:108px}
.plans tbody tr{height:28.5px}
.plans td.service{background:var(--cyan);color:#fff;font-size:17.5px;padding-left:16px;white-space:nowrap;line-height:1;overflow:hidden}
.plans td.cell{text-align:center;font-size:15px;font-weight:300;color:var(--muted)}
.tick{display:inline-block;width:20px;height:10px;border-left:4px solid var(--tick);border-bottom:4px solid var(--tick);transform:rotate(-45deg) translate(2px,-2px)}
.wave{position:absolute;left:0;top:1010px;width:852px;height:190px}
.footer{position:absolute;left:24px;right:24px;top:1153px;display:flex;justify-content:space-between;align-items:center;color:#fff;font-size:16.5px;white-space:nowrap;letter-spacing:.2px}
.footer span{display:flex;align-items:center;gap:5px}
.footer svg{width:18px;height:18px;flex:none}
</style>
</head>
<body>
<div class="sheet">
  <div class="brand"><span class="brand-dot"></span><span class="brand-name">Silver Harbor Med Spa</span></div>
  <h1 class="title">AGELESS GLOW MEMBERSHIPS</h1>
  <div class="badge" role="img" aria-label="Award badge"></div>

  <div class="treat-bar">TREATMENTS</div>
  <div class="treat-sub">GREEN UNLIMIT OR PER MONTH</div>

  <table class="plans">
    <thead>
      <tr><th class="spacer"></th><th class="tier good">GOOD<br>$189</th><th class="tier better">BETTER<br>$289</th><th class="tier best">BEST<br>$389</th></tr>
    </thead>
    <tbody>
      <tr><td class="service">SKIN EVALUATION</td><td class="cell"><i class="tick"></i></td><td class="cell"><i class="tick"></i></td><td class="cell"><i class="tick"></i></td></tr>
      <tr><td class="service">INFRARED SAUNA</td><td class="cell"><i class="tick"></i></td><td class="cell"><i class="tick"></i></td><td class="cell"><i class="tick"></i></td></tr>
      <tr><td class="service">MASSAGE CHAIR</td><td class="cell"><i class="tick"></i></td><td class="cell"><i class="tick"></i></td><td class="cell"><i class="tick"></i></td></tr>
      <tr><td class="service">VIBRATIONAL LYMPHATIC PLATE</td><td class="cell"><i class="tick"></i></td><td class="cell"><i class="tick"></i></td><td class="cell"><i class="tick"></i></td></tr>
      <tr><td class="service">MEDICAL FACIAL</td><td class="cell"><i class="tick"></i></td><td class="cell"><i class="tick"></i></td><td class="cell"><i class="tick"></i></td></tr>
      <tr><td class="service">FACE LYMPHATIC DRAINAGE</td><td class="cell"><i class="tick"></i></td><td class="cell"><i class="tick"></i></td><td class="cell"><i class="tick"></i></td></tr>
      <tr><td class="service">RED LIGHT THERAPY</td><td class="cell"><i class="tick"></i></td><td class="cell"><i class="tick"></i></td><td class="cell"><i class="tick"></i></td></tr>
      <tr><td class="service">PH OXYGEN SERUM</td><td class="cell"><i class="tick"></i></td><td class="cell"><i class="tick"></i></td><td class="cell"><i class="tick"></i></td></tr>
      <tr><td class="service">CHEMICAL PEELS PROGRESSIVE OR MIDDEPTH</td><td class="cell"><i class="tick"></i></td><td class="cell"><i class="tick"></i></td><td class="cell"><i class="tick"></i></td></tr>
      <tr><td class="service">LUMORA LIGHT AGELESS GLOW</td><td class="cell"><i class="tick"></i></td><td class="cell"><i class="tick"></i></td><td class="cell"><i class="tick"></i></td></tr>
      <tr><td class="service">LUMORA 2 CORRECTION PASSES</td><td class="cell"><i class="tick"></i></td><td class="cell"><i class="tick"></i></td><td class="cell"><i class="tick"></i></td></tr>
      <tr><td class="service">DERMAPLANING</td><td class="cell"></td><td class="cell"><i class="tick"></i></td><td class="cell"><i class="tick"></i></td></tr>
      <tr><td class="service">VITAMIN A PEEL</td><td class="cell"></td><td class="cell"><i class="tick"></i></td><td class="cell"><i class="tick"></i></td></tr>
      <tr><td class="service">LUMORA UP TO 10 CORRECTION PASSES</td><td class="cell"></td><td class="cell"><i class="tick"></i></td><td class="cell"><i class="tick"></i></td></tr>
      <tr><td class="service">LUMORA HAIR REMOVAL</td><td class="cell"></td><td class="cell"><i class="tick"></i></td><td class="cell"><i class="tick"></i></td></tr>
      <tr><td class="service">MICRONEEDLING</td><td class="cell"></td><td class="cell"><i class="tick"></i></td><td class="cell"><i class="tick"></i></td></tr>
      <tr><td class="service">LUMORA FIRMTONE</td><td class="cell"></td><td class="cell"></td><td class="cell"><i class="tick"></i></td></tr>
      <tr><td class="service">MICRONEEDLING PDO RADIANCE</td><td class="cell"></td><td class="cell"></td><td class="cell"><i class="tick"></i></td></tr>
      <tr><td class="service">CHEMICAL PEEL VERANO ITALIAN</td><td class="cell"></td><td class="cell"></td><td class="cell"><i class="tick"></i></td></tr>
      <tr><td class="service">TRIMWAVE TARGETED WEIGHT LOSS</td><td class="cell"></td><td class="cell"></td><td class="cell"><i class="tick"></i></td></tr>
      <tr><td class="service">LASER REJUVENATION</td><td class="cell">10% OFF</td><td class="cell">20% OFF</td><td class="cell">30% OFF</td></tr>
      <tr><td class="service">PLASMA PEN</td><td class="cell">10% OFF</td><td class="cell">20% OFF</td><td class="cell">30% OFF</td></tr>
      <tr><td class="service">HYPERBARIC OXYGEN</td><td class="cell">10% OFF</td><td class="cell">20% OFF</td><td class="cell">30% OFF</td></tr>
      <tr><td class="service">MASSAGE</td><td class="cell">10% OFF</td><td class="cell">20% OFF</td><td class="cell">30% OFF</td></tr>
      <tr><td class="service">AIRBRUSH TANNING</td><td class="cell">10% OFF</td><td class="cell">20% OFF</td><td class="cell">30% OFF</td></tr>
      <tr><td class="service">IONIC DETOX</td><td class="cell">10% OFF</td><td class="cell">20% OFF</td><td class="cell">30% OFF</td></tr>
      <tr><td class="service">LYMPHATIC DRAINAGE</td><td class="cell">10% OFF</td><td class="cell">20% OFF</td><td class="cell">30% OFF</td></tr>
      <tr><td class="service">TIRZEPATIDE WEIGHT</td><td class="cell">10% OFF</td><td class="cell">20% OFF</td><td class="cell">30% OFF</td></tr>
      <tr><td class="service">LIP FILLERS NEEDLE-LESS</td><td class="cell">10% OFF</td><td class="cell">20% OFF</td><td class="cell">30% OFF</td></tr>
    </tbody>
  </table>

  <svg class="wave" viewBox="0 0 852 190" preserveAspectRatio="none" aria-hidden="true">
    <path d="M0 100 C 200 60, 420 110, 620 95 C 740 86, 820 40, 852 0 L852 190 L0 190 Z" fill="var(--cyan-soft)"/>
    <path d="M0 140 C 160 85, 380 110, 560 125 C 700 136, 800 110, 852 60 L852 190 L0 190 Z" fill="var(--cyan)"/>
  </svg>

  <div class="footer">
    <span><svg viewBox="0 0 24 24"><path fill="#fff" d="M6.6 10.8a15 15 0 0 0 6.6 6.6l2.2-2.2c.3-.3.7-.4 1-.2 1.1.4 2.3.6 3.6.6.6 0 1 .4 1 1V20c0 .6-.4 1-1 1A17 17 0 0 1 3 4c0-.6.4-1 1-1h3.5c.6 0 1 .4 1 1 0 1.3.2 2.5.6 3.6.1.3 0 .7-.2 1z"/></svg>972-555-0148</span>
    <span><svg viewBox="0 0 24 24" fill="none" stroke="#fff" stroke-width="1.6"><circle cx="12" cy="12" r="9"/><ellipse cx="12" cy="12" rx="4" ry="9"/><path d="M3 12h18M4.5 7.5h15M4.5 16.5h15"/></svg>silverharbormedspa.com</span>
    <span><svg viewBox="0 0 24 24"><path fill="#fff" d="M12 2a7 7 0 0 0-7 7c0 5.2 7 13 7 13s7-7.8 7-13a7 7 0 0 0-7-7zm0 9.5A2.5 2.5 0 1 1 12 6.5a2.5 2.5 0 0 1 0 5z"/></svg>1800 Harbor Point Dr. Addison, TX 75001</span>
  </div>
</div>
</body>
</html>
```